Business Card Design for BrightvaleMedia.com

--I need a business card design for my company BrightvaleMedia.com

I have attached my logo...I want the brightvale media logo on the front of the business card, and then I want The Quillstone Chief on the back of it with my information.

I would like to see a light colored background as well as a dark colored background

FRONT:
BRIGHTVALE MEDIA LOGO
248 N. Larkmoor
3rd Floor
San Diego CA 92173
www.BrightvaleMedia.com

Advanced Website & App Development
Websites, Apps, Online Voucher Systems

Leading Edge Marketing Services
SMS, VB, SMM, SEM,

BACK:
QUILLSTONE CHIEF LOGO
Dorian Pelletta
The Quillstone Chief
Call Or Text: 619-555-0148
Dorian@QuillstoneChief.example
www.QuillstoneChief.example

Target Market(s)

small business owners

Industry/Entity Type

Business Consultant

Contact Information for Business Card

FRONT:
BRIGHTVALE MEDIA LOGO
248 N. Larkmoor
3rd Floor
San Diego CA 92173
www.BrightvaleMedia.com

SMS, VB, SMM, SEM,

BACK:
QUILLSTONE CHIEF LOGO
Dorian Pelletta
The Quillstone Chief
Dorian@QuillstoneChief.example
www.QuillstoneChief.example

Requirements
Must have
• add this quote on it somewhere, anywhere,preferrably on back
• "The Fastest Way To Success Is To Take Action”
• — Dorian Pelletta, Quillstone Chief
Nice to have
• open
Should not have
• red

```html
<!DOCTYPE html>
<html lang="en">
<head>
<meta charset="utf-8">
<title>Brightvale Media — Business Card</title>
<link rel="stylesheet" href="https://fonts.googleapis.com/css2?family=Open+Sans:ital,wght@0,400;0,600;0,700;1,400&display=swap">
<style>
  :root {
    --stage: #4a4a4a;
    --brand-blue: #0a6aa8;
    --card-white: #ffffff;
    --ink-grey: #5f6166;
    --band-grey: #6b6c70;
    --divider: #d4d6d9;
    --text-light: #ffffff;
  }
  * { box-sizing: border-box; margin: 0; padding: 0; }
  html, body {
    width: 1105px; height: 1200px; overflow: hidden;
    background: var(--stage);
    font-family: "Open Sans", Arial, sans-serif;
  }
  .card {
    position: absolute; left: 196px; width: 720px; height: 411px;
    box-shadow: 0 4px 10px rgba(0,0,0,.45);
  }
  .card--front {
    top: 146px; background: var(--brand-blue); color: var(--text-light);
    text-align: center;
  }
  .card--back { top: 602px; background: var(--card-white); overflow: hidden; }

  .front-wordmark {
    position: absolute; top: 80px; left: 0; right: 0;
    font-size: 34px; font-weight: 400; letter-spacing: 5px; line-height: 1;
  }
  .front-details { position: absolute; top: 172px; left: 0; right: 0; font-size: 19px; line-height: 26px; }
  .front-details .web { font-weight: 700; }
  .front-details .group { margin-top: 14px; }

  .back-quote {
    position: absolute; top: 38px; left: 40px; right: 40px;
    text-align: center; color: var(--ink-grey);
    font-size: 15px; line-height: 22px; font-style: italic;
  }
  .back-wordmark {
    position: absolute; left: 24px; width: 310px; top: 186px;
    text-align: center; color: var(--brand-blue);
    font-size: 26px; font-weight: 700; letter-spacing: 2px; line-height: 1;
  }
  .back-divider {
    position: absolute; left: 352px; top: 123px; width: 1px; height: 166px;
    background: var(--divider);
  }
  .back-info { position: absolute; left: 372px; top: 124px; right: 24px; color: var(--ink-grey); }
  .back-name { color: var(--brand-blue); font-size: 25px; font-weight: 600; line-height: 32px; }
  .back-title { font-size: 19px; line-height: 28px; margin-bottom: 14px; }
  .contact-list { list-style: none; font-size: 17px; line-height: 28px; }
  .contact-list li { display: flex; align-items: center; gap: 10px; white-space: nowrap; }
  .contact-list svg { width: 15px; height: 15px; fill: var(--brand-blue); flex: none; }
  .back-band { position: absolute; left: 0; bottom: 0; width: 720px; height: 26px; }
</style>
</head>
<body>
  <section class="card card--front" aria-label="Card front">
    <div class="front-wordmark">BRIGHTVALE MEDIA</div>
    <div class="front-details">
      <p>248 N. Larkmoor, 3rd Floor, San Diego CA 92173</p>
      <p class="web">www.BrightvaleMedia.com</p>
      <div class="group">
        <p>Advanced Website &amp; App Development</p>
        <p>Websites • Apps • Online Voucher Systems</p>
      </div>
      <div class="group">
        <p>Leading Edge Marketing Services</p>
        <p>SMS • VB • SMM • SEM</p>
      </div>
    </div>
  </section>

  <section class="card card--back" aria-label="Card back">
    <p class="back-quote">“The Fastest Way To Success Is To Take Action”<br>— Dorian Pelletta, Quillstone Chief</p>
    <div class="back-wordmark">QUILLSTONE CHIEF</div>
    <div class="back-divider"></div>
    <div class="back-info">
      <p class="back-name">Dorian Pelletta</p>
      <p class="back-title">The Quillstone Chief</p>
      <ul class="contact-list">
        <li><svg viewBox="0 0 16 16" aria-hidden="true"><path d="M3.6 1.2l2.3 2.6-1.3 1.8c.9 2 2.7 3.8 4.7 4.7l1.8-1.3 2.6 2.3-1.4 2.2C6.6 14.4 1.6 9.4 1.5 3.6z"/></svg>619-555-0148</li>
        <li><svg viewBox="0 0 16 16" aria-hidden="true"><path d="M1 3h14v10H1z M2 4.5v.3l6 4 6-4v-.3z" fill-rule="evenodd"/></svg>Dorian@QuillstoneChief.example</li>
        <li><svg viewBox="0 0 16 16" aria-hidden="true"><circle cx="8" cy="8" r="7"/><path d="M4 5c2 0 2 2 4 2s1 3 3 3M9 2c0 2 2 2 3 3" stroke="#fff" stroke-width="1.2" fill="none"/></svg>www.QuillstoneChief.example</li>
      </ul>
    </div>
    <svg class="back-band" viewBox="0 0 720 26" aria-hidden="true">
      <polygon points="0,0 467,0 460,26 0,26" fill="var(--brand-blue)"/>
      <polygon points="474,0 720,0 720,26 467,26" fill="var(--band-grey)"/>
    </svg>
  </section>
</body>
</html>
```